Ad Design for a child care centre

Bright Owlets Child Care Centre offers a safe, nurturing environment where your child will get the attention and care that he or she needs. Our ratio of children to adults is always within state guidelines - and often even higher - to make certain each child receives top-quality care
We are also state licensed as a Child Care facility and have met or exceeded all health and safety guidelines.
3-5 year Kinder Funded Program
Story Time
Show and Tell
Puzzles and Games
Computer Time
Arts and Crafts
Music
Pre-Reading Activities
And much more
You can rest assured that your child will be cared for with the most kindness, love and respect. We believe all children are precious gifts and we treat them as though they are our own.
Full-time, part-time, Half days, Before, after-school schedules are available.
To learn more, contact us today! 03 9461 -0287 or info@brightowlets.example.com.au

```html
<!DOCTYPE html>
<html lang="en">
<head>
<meta charset="utf-8">
<title>Bright Owlets Child Care and Kinder – Flyer</title>
<link rel="stylesheet" href="https://fonts.googleapis.com/css2?family=Ubuntu:wght@400;500;700&family=Gochi+Hand&display=swap">
<style>
  :root {
    --teal: #3f8c86;
    --teal-text: #2f8f89;
    --coral: #f26f63;
    --orange: #f2a852;
    --brick: #d4503b;
    --butter: #f3d780;
    --sky: #c3e5f4;
    --ink: #2b2b2b;
    --phone-red: #c41e3a;
    --logo-purple: #5b2c83;
    --pink: #f07ab4;
    --white: #ffffff;
  }
  * { box-sizing: border-box; margin: 0; padding: 0; }
  html, body { width: 988px; height: 1200px; overflow: hidden; background: var(--white); }
  body { font-family: "Ubuntu", sans-serif; color: var(--ink); position: relative; }

  /* Top mosaic */
  .mosaic {
    position: absolute; top: 0; left: 0; width: 988px; height: 360px;
    display: grid; grid-template-columns: repeat(5, 1fr); grid-template-rows: repeat(2, 1fr);
  }
  .tile--teal { background: var(--teal); }
  .tile--coral { background: var(--coral); }
  .tile--orange { background: var(--orange); }
  .tile--brick { background: var(--brick); }
  .tile--butter { background: var(--butter); }
  .tile--photo { background: linear-gradient(150deg, #c9b39a, #8d7a66); }
  .tile--photo-green { background: linear-gradient(150deg, #7d9a62, #c7a88b); }
  .tile--photo-warm { background: linear-gradient(150deg, #d6c2b0, #a07b63); }

  /* Feature band */
  .feature {
    position: absolute; top: 368px; left: 0; width: 988px; height: 300px;
    background: linear-gradient(100deg, #6d6d6d, #a5a5a5 45%, #5a5a5a);
    border-top: 4px solid var(--white); border-bottom: 4px solid var(--white);
  }
  .brand-disc {
    position: absolute; top: 388px; left: 40px; width: 340px; height: 276px;
    background: var(--white); border-radius: 50%;
    display: flex; flex-direction: column; align-items: center; justify-content: center;
    text-align: center; padding-top: 6px;
  }
  .brand-name {
    font-weight: 700; font-size: 42px; line-height: 1.05; color: var(--logo-purple);
  }
  .brand-tagline { margin-top: 12px; font-size: 18px; line-height: 1.3; color: var(--ink); }
  .offer {
    position: absolute; top: 505px; left: 530px; width: 440px; height: 120px;
    background: rgba(20, 20, 20, 0.85); padding: 10px 20px;
  }
  .offer-lead { font-size: 33px; color: var(--white); font-weight: 400; }
  .offer-deal { font-family: "Gochi Hand", cursive; font-size: 46px; color: var(--pink); line-height: 1.1; }

  /* Info blocks */
  .intro {
    position: absolute; top: 672px; left: 0; width: 610px; height: 215px;
    background: var(--teal); color: var(--white); padding: 30px 30px;
    font-weight: 700; font-size: 17px; line-height: 1.45;
  }
  .program {
    position: absolute; top: 672px; left: 610px; width: 378px; height: 215px;
    background: var(--coral); color: var(--white); padding: 15px 24px 12px;
    font-weight: 700; font-size: 15.5px; line-height: 1.3;
  }
  .program-list { list-style: none; }
  .program-list li::before { content: "• "; }

  .assurance {
    position: absolute; top: 887px; left: 0; width: 988px; height: 165px;
    background: var(--sky); padding: 18px 30px 0;
  }
  .assurance-cols { display: flex; align-items: stretch; height: 96px; }
  .assurance-col { font-size: 15.5px; line-height: 1.4; }
  .assurance-col--left { width: 345px; padding-top: 20px; }
  .assurance-divider { width: 2px; background: #6a7a80; margin: 0 28px; }
  .assurance-col--right { flex: 1; }
  .schedules { margin-top: 16px; font-size: 20px; text-align: center; }

  /* Contact footer */
  .contact {
    position: absolute; top: 1052px; left: 0; width: 988px; height: 148px;
    display: flex; justify-content: space-between; align-items: center; padding: 0 50px 0 110px;
  }
  .contact-call { font-weight: 500; font-size: 34px; line-height: 1.25; color: var(--teal-text); text-align: center; }
  .contact-details { text-align: center; }
  .contact-phone { font-weight: 700; font-size: 46px; line-height: 1.15; color: var(--phone-red); letter-spacing: 1px; }
  .contact-line { font-size: 17px; letter-spacing: 1px; margin-top: 6px; }
</style>
</head>
<body>
  <section class="mosaic">
    <div class="tile tile--teal"></div>
    <div class="tile tile--photo" role="img" aria-label="Photo of a smiling toddler in a blue cap"></div>
    <div class="tile tile--coral"></div>
    <div class="tile tile--photo-warm" role="img" aria-label="Photo of a laughing baby in a classroom"></div>
    <div class="tile tile--orange"></div>
    <div class="tile tile--photo-green" role="img" aria-label="Photo of a baby outdoors"></div>
    <div class="tile tile--brick"></div>
    <div class="tile tile--photo-green" role="img" aria-label="Photo of two sisters at a playground"></div>
    <div class="tile tile--butter"></div>
    <div class="tile tile--photo-warm" role="img" aria-label="Photo of a child with face paint"></div>
  </section>

  <section class="feature" role="img" aria-label="Black and white photo of children sitting together on a classroom floor"></section>

  <div class="brand-disc">
    <p class="brand-name">Bright Owlets<br>Child Care<br>and Kinder</p>
    <p class="brand-tagline">We are not just a child Care<br>Centre we are Family</p>
  </div>

  <div class="offer">
    <p class="offer-lead">book in now for your</p>
    <p class="offer-deal">50% off Special..</p>
  </div>

  <section class="intro">
    Bright Owlets Child Care Centre offers a safe, nurturing environment where your child will get the attention and care that he or she needs. Our ratio of children to adults is always within state guidelines - and often even higher - to make certain each child receives top-quality care
  </section>

  <section class="program">
    <p>3-5 year Kinder Funded Program</p>
    <ul class="program-list">
      <li>Story Time</li>
      <li>Show and Tell</li>
      <li>Puzzles and Games</li>
      <li>Computer Time</li>
      <li>Arts and Crafts</li>
      <li>Music</li>
      <li>Pre-Reading Activities</li>
      <li>And much more</li>
    </ul>
  </section>

  <section class="assurance">
    <div class="assurance-cols">
      <p class="assurance-col assurance-col--left">We are also state licensed as a Child Care facility and have met or exceeded all health and safety guidelines.</p>
      <div class="assurance-divider"></div>
      <p class="assurance-col assurance-col--right">You can rest assured that your child will be cared for with the most kindness, love and respect. We believe all children are precious gifts and we treat them as though they are our own.</p>
    </div>
    <p class="schedules">Full-time, part-time, Half days, Before, after-school schedules are available.</p>
  </section>

  <footer class="contact">
    <p class="contact-call">To learn more<br>contact us today!</p>
    <div class="contact-details">
      <p class="contact-phone">03 9461 -0287</p>
      <p class="contact-line">or info@brightowlets.example.com.au</p>
      <p class="contact-line">www.brightowlets.example.com.au</p>
    </div>
  </footer>
</body>
</html>
```